Harbor Crest Holdings Corporate Showcase

Provide an attractive Corporate Website for a boutique Investment Company to showcase our activities and corporate interests.

Our Company works across a number of Sectors including

Real Estate
E-Commerce
Healthcare
Beauty & Personal Care
Technology
Resources

Lets keep the personality

Modern
Global
Sophisticated
Calm
Interesting

Lets keep the pages with MINIMAL Words
Lets use Photos/ Imagery to tell the story

We'll need a Banner Menu -
About Us
Expertise
Global Outlook
Sectors
Management
Media
Contact Us

Many thanks
Best wishes
Dennis.

Target Market(s)

Investors
Clients

Coding

Coded - Design and coding required

Number of Pages Required

5+ page

Font styles to use
Sans Serif

Colors
886aae
3176b5
00a990
f68e4d
f04a50
e667a6

Requirements
Must have
• WordPress Coding

Checkout this Website for look and feel - its cool:
www.qvr-example.com

Harbor Crest Partners
(Harbor Crest Holdings LLP)
London
E9 4ZX
United Kingdom

www.HarborCrestPartners-example.com
Nice to have
• Sophisticated colour palette - black/ brown/ blue/ purple/

```html
<!DOCTYPE html>
<html lang="en">
<head>
<meta charset="utf-8">
<title>Harbor Crest Holdings</title>
<link rel="stylesheet" href="https://fonts.googleapis.com/css2?family=IBM+Plex+Sans:wght@400;500;600;700&family=Rubik:wght@500;600;700;800&family=Poppins:wght@400;500&display=swap">
<style>
:root{
  --purple:#7b55a6;
  --blue:#2c62ae;
  --blue-dark:#1f4f93;
  --ink:#1d1d1f;
  --text:#333;
  --soft-bg:#f4f1f1;
  --footer:#2e2c2f;
  --white:#fff;
}
*{margin:0;padding:0;box-sizing:border-box}
html,body{width:1200px;height:2745px;overflow:hidden;background:var(--white)}
body{position:relative;font-family:"IBM Plex Sans",Arial,sans-serif;color:var(--text)}
.abs{position:absolute}
.btn{display:inline-block;background:var(--purple);color:var(--white);font-family:"Rubik",Arial,sans-serif;font-weight:700;text-transform:uppercase;text-align:center}
.brand{display:flex;align-items:center;gap:12px;font-family:"Rubik",Arial,sans-serif;font-weight:600;color:var(--blue);letter-spacing:.3px}
.brand-mark{width:44px;height:44px;border:3px solid var(--purple);border-radius:50%}

/* header */
.site-header{left:0;top:0;width:1200px;height:122px}
.site-header .brand{left:128px;top:18px;font-size:23px}
.follow{left:755px;top:34px;display:flex;align-items:center;gap:10px;font-size:10px;font-weight:500;color:var(--ink)}
.social-dot{width:27px;height:27px;border-radius:50%;background:var(--blue)}
.social-dot.dark{background:#111}
.call{left:907px;top:27px;display:flex;align-items:center;gap:12px}
.call-icon{width:34px;height:34px;border-radius:50%;background:var(--blue);display:flex;align-items:center;justify-content:center}
.call small{display:block;font-size:10px;font-weight:500;color:var(--ink)}
.call strong{display:block;font-size:18px;font-weight:500;color:var(--ink);line-height:1.1}
.main-nav{left:128px;top:88px;width:942px;display:flex;justify-content:space-between;font-size:14.5px;font-weight:500;color:var(--ink)}
.main-nav .active{color:var(--purple);text-decoration:underline;text-underline-offset:3px}

/* hero */
.hero{left:0;top:122px;width:1200px;height:556px;background:linear-gradient(180deg,#6f86a3 0%,#8a7a6c 45%,#5a4334 80%,#3a2a22 100%)}
.hero-title{left:0;top:168px;width:1200px;text-align:center;font-family:"Rubik",Arial,sans-serif;font-weight:800;font-size:46px;color:var(--white);letter-spacing:-.5px}
.hero-sub{left:0;top:228px;width:1200px;text-align:center;font-weight:600;font-size:18.5px;color:var(--white);letter-spacing:.3px}
.hero .btn{left:526px;top:273px;width:148px;height:46px;line-height:46px;font-size:17px}
.dots{left:557px;top:499px;display:flex;gap:12px;align-items:center}
.dots span{width:8px;height:8px;border-radius:50%;background:var(--white)}
.dots .on{width:12px;height:12px;background:none;border:2px solid var(--white)}

/* section heading */
.sec-title{left:0;width:1200px;text-align:center;font-family:"Rubik",Arial,sans-serif;font-weight:600;font-size:24px;color:var(--ink)}
.sec-title::after{content:"";display:block;width:50px;height:3px;background:var(--blue);margin:16px auto 0}

/* services */
.service{top:835px;width:302px;height:233px;border:2px solid var(--blue);text-align:center}
.service-icon{position:absolute;left:108px;top:-42px;width:86px;height:86px;border-radius:50%;background:var(--blue);display:flex;align-items:center;justify-content:center}
.service h3{margin-top:72px;font-family:"Rubik",Arial,sans-serif;font-weight:600;font-size:16px;color:var(--blue)}
.service p{margin:10px auto 0;width:215px;font-size:13.5px;line-height:18.5px}
.service .btn{margin-top:16px;width:91px;height:26px;line-height:26px;font-size:10px}

/* welcome */
.welcome{left:0;top:1136px;width:1200px;height:452px;background:var(--soft-bg)}
.hex-photo{left:147px;top:0;width:393px;height:452px}
.welcome-small{left:625px;top:48px;font-size:18px;font-weight:500;color:var(--ink)}
.welcome-title{left:624px;top:70px;font-family:"Rubik",Arial,sans-serif;font-weight:600;font-size:39px;color:var(--blue)}
.welcome-rule{left:625px;top:122px;width:50px;height:3px;background:var(--blue)}
.welcome-text{left:625px;top:154px;width:420px;font-size:16px;line-height:23.2px}
.welcome .btn{left:627px;top:367px;width:111px;height:34px;line-height:34px;font-size:12.5px}

/* sectors */
.sectors{left:0;top:1588px;width:1200px;height:360px;background:linear-gradient(160deg,#2b63b0 0%,#2a5fab 60%,#2458a3 100%)}
.sectors .sec-title{top:47px;color:var(--white)}
.sectors .sec-title::after{background:var(--white)}
.sector{top:134px;width:147px;height:164px;border:1px solid rgba(255,255,255,.75);display:flex;flex-direction:column;align-items:center;color:var(--white);font-family:"Poppins",Arial,sans-serif;font-size:15px;text-align:center;line-height:20px}
.sector svg{margin-top:32px;height:52px}
.sector span{margin-top:24px}
.sector span.two{margin-top:14px}

/* media */
.media-card{top:2089px;width:299px;height:263px;border:1px solid #d9d9d9;box-shadow:0 1px 4px rgba(0,0,0,.12);padding:32px 36px 0 30px}
.media-card time{display:block;font-size:11px;color:var(--ink)}
.media-card h3{margin-top:6px;font-family:"Rubik",Arial,sans-serif;font-weight:500;font-size:15.5px;line-height:20px;color:var(--ink)}
.media-card p{margin-top:16px;font-size:12.5px;line-height:17.6px}
.media-card .btn{margin-top:16px;width:76px;height:23px;line-height:23px;font-size:9px}

/* footer */
.site-footer{left:0;top:2410px;width:1200px;height:335px;background:var(--footer);color:#e6e6e6}
.site-footer .brand{left:130px;top:112px;font-size:23px}
.foot-head{top:54px;font-family:"Rubik",Arial,sans-serif;font-weight:600;font-size:13px;color:var(--white)}
.foot-menu{left:467px;top:90px;font-size:12px;line-height:19.8px;list-style:none}
.contact-item,.follow-item{display:flex;gap:10px;align-items:center;font-size:12px;line-height:15.5px}
.foot-icon{width:24px;height:24px;border-radius:50%;background:var(--white);flex:none;display:flex;align-items:center;justify-content:center}
.foot-rule{left:136px;top:273px;width:934px;height:1px;background:#4a474c}
.copyright{left:0;top:306px;width:1200px;text-align:center;font-size:10px}
</style>
</head>
<body>

<header class="site-header abs">
  <div class="brand abs"><span class="brand-mark"></span>HARBOR CREST</div>
  <div class="follow abs">FOLLOW US <span class="social-dot"></span><span class="social-dot dark"></span></div>
  <div class="call abs">
    <span class="call-icon"><svg width="18" height="18" viewBox="0 0 24 24"><path d="M6.6 10.8a15 15 0 0 0 6.6 6.6l2.2-2.2c.3-.3.7-.4 1-.2 1.1.4 2.3.6 3.6.6.6 0 1 .4 1 1V20c0 .6-.4 1-1 1A17 17 0 0 1 3 4c0-.6.4-1 1-1h3.5c.6 0 1 .4 1 1 0 1.3.2 2.5.6 3.6.1.3 0 .7-.2 1z" fill="#fff"/></svg></span>
    <div><small>CALL US</small><strong>555.014.2736</strong></div>
  </div>
  <nav class="main-nav abs">
    <span class="active">HOME</span><span>ABOUT US</span><span>EXPERTISE</span><span>GLOBAL OUTLOOK</span><span>SECTORS</span><span>MANAGEMENT</span><span>MEDIA</span><span>CONTACT US</span>
  </nav>
</header>

<section class="hero abs" role="img" aria-label="Upward view of city skyscrapers against a cloudy blue sky">
  <h1 class="hero-title abs">BOUTIQUE INVESTMENT</h1>
  <p class="hero-sub abs">LOREM IPSUM IS SIMPLY DUMMY TEXT OF THE PRINTING</p>
  <a class="btn abs">READ MORE</a>
  <div class="dots abs"><span></span><span></span><span class="on"></span><span></span><span></span></div>
</section>

<h2 class="sec-title abs" style="top:714px">OUR SERVICES</h2>

<article class="service abs" style="left:130px">
  <div class="service-icon"><svg width="50" height="50" viewBox="0 0 50 50" fill="none" stroke="#fff" stroke-width="2.5"><circle cx="25" cy="14" r="9"/><path d="M25 9v10M22 12h5M22 16h5M25 23v8M25 31c-5-1-8-4-8-7M25 31c5-1 8-4 8-7M6 34h8l6 4h10c2 0 2 3 0 3H20M14 44l8 2h10l12-8c2-1 0-4-2-3l-10 5"/></svg></div>
  <h3>INVESTMENT ADVISORY</h3>
  <p>Lorem ipsum dolor sit amet cons ectetur adipiscing eli sed do eiusmod tempor incid.</p>
  <a class="btn">READ MORE</a>
</article>
<article class="service abs" style="left:449px">
  <div class="service-icon"><svg width="46" height="46" viewBox="0 0 46 46" fill="none" stroke="#fff" stroke-width="2.5"><rect x="6" y="6" width="20" height="36"/><rect x="26" y="18" width="14" height="24"/><path d="M11 12h3M18 12h3M11 19h3M18 19h3M11 26h3M18 26h3M11 33h3M18 33h3M31 24h4M31 30h4M31 36h4"/></svg></div>
  <h3>ASSET MANAGEMENT</h3>
  <p>Lorem ipsum dolor sit amet cons ectetur adipiscing eli sed do eiusmod tempor incid.</p>
  <a class="btn">READ MORE</a>
</article>
<article class="service abs" style="left:766px">
  <div class="service-icon"><svg width="48" height="46" viewBox="0 0 48 46" fill="#fff"><rect x="4" y="30" width="7" height="12"/><rect x="14" y="24" width="7" height="18"/><rect x="24" y="18" width="7" height="24"/><rect x="34" y="12" width="7" height="30"/><path d="M4 22 30 6" stroke="#fff" stroke-width="3"/><path d="M26 3h9v9z"/></svg></div>
  <h3>GROWTH CAPITAL</h3>
  <p>Lorem ipsum dolor sit amet cons ectetur adipiscing eli sed do eiusmod tempor incid.</p>
  <a class="btn">READ MORE</a>
</article>

<section class="welcome abs">
  <svg class="hex-photo abs" viewBox="0 0 393 452" role="img" aria-label="Hand holding a pen beside a laptop and printed financial charts">
    <defs><linearGradient id="deskTone" x1="0" y1="0" x2="1" y2="1"><stop offset="0" stop-color="#5a6470"/><stop offset=".5" stop-color="#c9ced4"/><stop offset="1" stop-color="#8d97a3"/></linearGradient></defs>
    <polygon points="196,0 393,113 393,339 196,452 0,339 0,113" fill="url(#deskTone)"/>
  </svg>
  <p class="welcome-small abs">WELCOME TO</p>
  <h2 class="welcome-title abs">HARBOR CREST</h2>
  <div class="welcome-rule abs"></div>
  <p class="welcome-text abs">At vero eos et accusamus et iusto odio dignissimos ducimus qui blanditiis praesentium voluptatum deleniti atque corrupti quos dolores et quas molestias excepturi sint occaecati cupiditate non provident, similique sunt in culpa qui officia deserunt mollitia animi, id est laborum et dolorum fuga. Et harum quidem rerum facilis est et expedita distinctio. Nam libero tempore, cum soluta nobis est eligendi optio cumque nihil impedit quo minus</p>
  <a class="btn abs">READ MORE</a>
</section>

<section class="sectors abs">
  <h2 class="sec-title abs">OUR SECTORS</h2>
  <div class="sector abs" style="left:130px"><svg viewBox="0 0 60 52" width="60" fill="none" stroke="#fff" stroke-width="3"><path d="M4 24 26 6l22 18M10 20v26h34V20M16 30h8v8h-8zM30 30h8v16"/><circle cx="46" cy="14" r="5"/></svg><span>Real Estate</span></div>
  <div class="sector abs" style="left:290px"><svg viewBox="0 0 56 52" width="56" fill="none" stroke="#fff" stroke-width="4"><path d="M3 5h9l7 28h28l5-18H15"/><circle cx="22" cy="44" r="4" fill="#fff"/><circle cx="42" cy="44" r="4" fill="#fff"/></svg><span>E-Commerce</span></div>
  <div class="sector abs" style="left:449px"><svg viewBox="0 0 56 52" width="56" fill="none" stroke="#fff" stroke-width="3"><path d="M28 30C16 22 12 16 14 10c2-6 10-7 14-1 4-6 12-5 14 1 2 6-2 12-14 20z"/><path d="M14 18h8l3-4 4 8 3-4h10"/><path d="M2 38h10l8 4h10M12 48l8 2h12l18-10"/></svg><span>Healthcare</span></div>
  <div class="sector abs" style="left:608px"><svg viewBox="0 0 50 56" width="48" fill="none" stroke="#fff" stroke-width="3"><path d="M10 30V20a15 15 0 0 1 30 0v10"/><ellipse cx="25" cy="24" rx="11" ry="13"/><path d="M6 54c0-10 8-15 19-15s19 5 19 15"/></svg><span class="two">Beauty &amp;<br>Personal Care</span></div>
  <div class="sector abs" style="left:765px"><svg viewBox="0 0 56 52" width="56" fill="none" stroke="#fff" stroke-width="3.5"><rect x="4" y="4" width="48" height="32" rx="3"/><path d="M28 36v8M16 46h24"/></svg><span>Technology</span></div>
  <div class="sector abs" style="left:922px"><svg viewBox="0 0 56 56" width="54" fill="none" stroke="#fff" stroke-width="3.5"><circle cx="22" cy="22" r="17"/><circle cx="22" cy="18" r="5" fill="#fff"/><path d="M13 30c2-5 16-5 18 0"/><path d="M35 35l14 14" stroke-width="7"/></svg><span>Resources</span></div>
</section>

<h2 class="sec-title abs" style="top:2003px">MEDIA</h2>

<article class="media-card abs" style="left:122px">
  <time>MAY 25,2020</time>
  <h3>Sed ut perspiciatis unde omnis iste natus error</h3>
  <p>At vero eos et accusamus et iusto odio dignissimos ducimus qui blanditiis praes entium voluptatum deleniti atque corru pti quos dolores et quas molestias excepturi sint occaecati.</p>
  <a class="btn">READ MORE</a>
</article>
<article class="media-card abs" style="left:451px">
  <time>MAY 25,2020</time>
  <h3>Sed ut perspiciatis unde omnis iste natus error</h3>
  <p>At vero eos et accusamus et iusto odio dignissimos ducimus qui blanditiis praes entium voluptatum deleniti atque corru pti quos dolores et quas molestias excepturi sint occaecati.</p>
  <a class="btn">READ MORE</a>
</article>
<article class="media-card abs" style="left:778px">
  <time>MAY 25,2020</time>
  <h3>Sed ut perspiciatis unde omnis iste natus error</h3>
  <p>At vero eos et accusamus et iusto odio dignissimos ducimus qui blanditiis praes entium voluptatum deleniti atque corru pti quos dolores et quas molestias excepturi sint occaecati.</p>
  <a class="btn">READ MORE</a>
</article>

<footer class="site-footer abs">
  <div class="brand abs"><span class="brand-mark"></span>HARBOR CREST</div>

  <h4 class="foot-head abs" style="left:467px">MENU</h4>
  <ul class="foot-menu abs">
    <li>HOME</li><li>ABOUT US</li><li>EXPERTISE</li><li>GLOBAL OUTLOOK</li><li>SECTORS</li><li>MANAGEMENT</li><li>MEDIA</li><li>CONTACT US</li>
  </ul>

  <h4 class="foot-head abs" style="left:683px">CONTACT US</h4>
  <div class="contact-item abs" style="left:682px;top:92px"><span class="foot-icon"><svg width="10" height="13" viewBox="0 0 10 13"><path d="M5 0a5 5 0 0 0-5 5c0 3.5 5 8 5 8s5-4.5 5-8a5 5 0 0 0-5-5z" fill="#2e2c2f"/><circle cx="5" cy="5" r="1.8" fill="#fff"/></svg></span><span>2150 Linden Avenue<br>Riverton, CA 90210</span></div>
  <div class="contact-item abs" style="left:682px;top:143px"><span class="foot-icon"><svg width="12" height="12" viewBox="0 0 24 24"><path d="M6.6 10.8a15 15 0 0 0 6.6 6.6l2.2-2.2c.3-.3.7-.4 1-.2 1.1.4 2.3.6 3.6.6.6 0 1 .4 1 1V20c0 .6-.4 1-1 1A17 17 0 0 1 3 4c0-.6.4-1 1-1h3.5c.6 0 1 .4 1 1 0 1.3.2 2.5.6 3.6.1.3 0 .7-.2 1z" fill="#2e2c2f"/></svg></span><span>Call Us<br>555.014.2736</span></div>
  <div class="contact-item abs" style="left:682px;top:194px"><span class="foot-icon"><svg width="12" height="9" viewBox="0 0 12 9"><rect width="12" height="9" rx="1" fill="#2e2c2f"/><path d="M0 1l6 4 6-4" stroke="#fff" fill="none"/></svg></span><span>E mail Us<br>info@HarborCrest-example.com</span></div>

  <h4 class="foot-head abs" style="left:965px">FOLLOW US</h4>
  <div class="follow-item abs" style="left:964px;top:92px"><span class="foot-icon"></span><span>Like us on<br>SOCIAL ONE</span></div>
  <div class="follow-item abs" style="left:964px;top:143px"><span class="foot-icon"></span><span>Follow us on<br>SOCIAL TWO</span></div>
  <div class="follow-item abs" style="left:964px;top:194px"><span class="foot-icon"></span><span>Follow us on<br>SOCIAL THREE</span></div>

  <div class="foot-rule abs"></div>
  <p class="copyright abs">Copyright © 2020 All Rights Reserved</p>
</footer>

</body>
</html>
```